Bed Company needs business card

Hello, we are a bed company that makes specialized magnets for beds. We are an alternative healing company. I need a modern and upscale business card. Please incorporate my logo for the card.

Accepted file formats are AI, EPS, and Press-Ready PDFS.

Please include all fonts or convert them to outlines regardless of file type.

If you are designing the card in Photoshop the file Must be 1200dpi.

I am open to anything for the business card.  I really like all of your designs and if you want to change the color of the logo, you can.  I will be making the final selection by Friday.  Thank You for all of your designs.  Feel Free to submit different color logos if you want.  

Reason: I will make a decision Final on Friday April 20th. 2012. Good Luck and Thank you all for the designs.

Target Market(s)

My target Market is people, who are looking for alternative healing.

Industry/Entity Type

Business

Requirements
Must have
• My logo must be incorporated. The front card must have

Name
Job Title

Address
Work
Cell
Fax
email
web

Just put in fake info for the card.

The back of the card. I want the logo on the back with color. I just want it to look modern and cool.

```html
<!DOCTYPE html>
<html lang="en">
<head>
<meta charset="utf-8">
<title>Restwell Field – Business Card</title>
<link rel="stylesheet" href="https://fonts.googleapis.com/css2?family=Open+Sans:wght@400;600;700&display=swap">
<style>
  :root {
    --backdrop: #4a4a4c;
    --card-white: #ffffff;
    --green-light: #5cbd4e;
    --green-mid: #45a845;
    --green-dark: #2f8a3c;
    --brand-green: #3f9f3f;
    --ink: #3b3b3b;
    --ink-soft: #555555;
    --title-green: #2b6e31;
  }
  * { margin: 0; padding: 0; box-sizing: border-box; }
  html, body {
    width: 1200px;
    height: 800px;
    overflow: hidden;
    background: var(--backdrop);
    font-family: "Open Sans", Arial, sans-serif;
  }
  .canvas {
    position: relative;
    width: 1200px;
    height: 800px;
    display: flex;
    align-items: center;
    justify-content: center;
    gap: 60px;
  }
  .card {
    position: relative;
    width: 520px;
    height: 297px;
    overflow: hidden;
    box-shadow: 0 10px 28px rgba(0, 0, 0, 0.35);
  }

  /* Front: contact side */
  .card-front { background: var(--card-white); }
  .front-band {
    position: absolute;
    inset: 0;
    background: linear-gradient(180deg, var(--green-light) 0%, var(--green-mid) 60%, var(--green-dark) 100%);
    clip-path: polygon(26% 0, 100% 0, 100% 80%);
  }
  .person {
    position: absolute;
    top: 34px;
    right: 70px;
    text-align: center;
  }
  .person-name {
    font-size: 26px;
    font-weight: 400;
    color: var(--ink);
    line-height: 1.1;
  }
  .person-title {
    font-size: 14px;
    color: var(--title-green);
    margin-top: 2px;
  }
  .brand {
    display: flex;
    align-items: center;
    gap: 7px;
  }
  .brand-mark {
    width: 20px;
    height: 20px;
    background: var(--brand-green);
  }
  .brand-name {
    font-weight: 700;
    color: var(--brand-green);
    line-height: 1;
  }
  .front-brand {
    position: absolute;
    top: 88px;
    left: 36px;
  }
  .front-brand .brand-name { font-size: 19px; }
  .contacts {
    position: absolute;
    top: 148px;
    left: 60px;
    font-size: 12.5px;
    color: var(--ink-soft);
    line-height: 1.45;
  }
  .contact-row { display: flex; }
  .contact-label { width: 34px; }
  .contact-sep { width: 16px; }
  .contact-web { margin-top: 8px; }
  .event {
    position: absolute;
    left: 60px;
    bottom: 22px;
    font-size: 11px;
    color: var(--ink-soft);
  }

  /* Back: brand side */
  .card-back {
    background: linear-gradient(180deg, var(--green-light) 0%, var(--green-mid) 55%, var(--green-dark) 100%);
    display: flex;
    align-items: center;
    justify-content: center;
  }
  .back-brand {
    margin-top: -30px;
  }
  .back-brand .brand-mark {
    width: 34px;
    height: 34px;
    background: var(--card-white);
  }
  .back-brand .brand-name {
    font-size: 32px;
    color: var(--card-white);
  }
</style>
</head>
<body>
  <main class="canvas">
    <section class="card card-front" aria-label="Business card front">
      <div class="front-band"></div>
      <div class="person">
        <p class="person-name">Daniel Hart</p>
        <p class="person-title">director</p>
      </div>
      <div class="front-brand">
        <div class="brand">
          <span class="brand-mark"></span>
          <span class="brand-name">Restwell Field</span>
        </div>
      </div>
      <div class="contacts">
        <p class="contact-row"><span class="contact-label">tel</span><span class="contact-sep">:</span><span>(999) 999 999</span></p>
        <p class="contact-row"><span class="contact-label">cell</span><span class="contact-sep">:</span><span>(999) 999 000</span></p>
        <p class="contact-row"><span class="contact-label">fax</span><span class="contact-sep">:</span><span>(999) 000 000</span></p>
        <p class="contact-web">office@restwellfield.com<br>www.restwell-field.com</p>
      </div>
      <p class="event">June 5-8, 2012, Lakeview Hall East, Riverton IL, Booth 2210</p>
    </section>

    <section class="card card-back" aria-label="Business card back">
      <div class="back-brand">
        <div class="brand">
          <span class="brand-mark"></span>
          <span class="brand-name">Restwell Field</span>
        </div>
      </div>
    </section>
  </main>
</body>
</html>
```